Building company buisness cards

We are looking for a sharp modern new look for our business cards.
We are a New Zealand based company that specialises in house and land packages.
We have attached a photo of the current logo and would like to see if it can be improved somehow if needed.
We are open to any colours but we have chosen green at this stage.
Feel free to change the font and make the logo smarter looking.
Play with the colours and see what looks best.

We want a card that looks so good know one will want to throw it away!

Target Market(s)

Home buyers

Industry/Entity Type

Building

Contact Information for Business Card

Derek Tolvane
0217394062
dtolvane@quillmarkhomesteads.co.nz
quillmarkhomesteads.co.nz

Font styles to use
Serif
Sans Serif

Colors

Designer to choose colors to be used in the design.

Requirements
Must have
• Logo and company name on one side, details on the other side
Nice to have
• Color codes for the original green are HEX #4a8028, RGB(74,128,40), CMYK(42,0,69,50)
• Round corners, Raised and/or spot UV

```html
<!DOCTYPE html>
<html lang="en">
<head>
<meta charset="utf-8">
<title>Quillmark Homesteads – Business Cards</title>
<link href="https://fonts.googleapis.com/css2?family=Nunito:wght@900&family=Arimo:wght@700&family=Open+Sans:wght@400&display=swap" rel="stylesheet">
<style>
  :root {
    --brand-green: #4a8028;
    --brand-tint: #dbe8d2;
    --swoosh-grey: #6b6b6b;
    --backdrop: #c9cacc;
    --card-white: #ffffff;
    --ink: #1e1e1e;
  }
  * { margin: 0; padding: 0; box-sizing: border-box; }
  html, body { width: 1200px; height: 940px; overflow: hidden; }
  body { background: var(--backdrop); position: relative; font-family: "Open Sans", sans-serif; }

  .card {
    position: absolute;
    width: 637px;
    height: 363px;
    border-radius: 30px;
    background: var(--card-white);
    overflow: hidden;
    box-shadow: 0 4px 10px rgba(0,0,0,0.28);
  }
  .card--front { left: 116px; top: 78px; }
  .card--back  { left: 423px; top: 506px; }

  .brand-square {
    position: absolute;
    background: var(--brand-tint);
  }
  .card--front .brand-square { left: 291px; top: 25px; width: 56px; height: 56px; }
  .card--back .brand-square { left: 40px; top: 12px; width: 340px; height: 340px; }

  .wordmark {
    position: absolute;
    font-family: "Nunito", sans-serif;
    font-weight: 900;
    color: var(--brand-green);
    text-align: center;
    line-height: 1;
    letter-spacing: -0.3px;
  }
  .wordmark__top { display: block; }
  .wordmark__bottom { display: block; margin-top: 3px; }

  .card--front .wordmark { left: 0; width: 637px; top: 90px; }
  .card--front .wordmark__top { font-size: 27px; }
  .card--front .wordmark__bottom { font-size: 36px; }

  .rule {
    position: absolute;
    height: 1.5px;
    background: var(--brand-green);
  }
  .card--front .rule { left: 259px; width: 111px; top: 167px; }

  .holder-name {
    position: absolute;
    left: 0; width: 637px; top: 191px;
    text-align: center;
    font-family: "Arimo", sans-serif;
    font-weight: 700;
    font-size: 26px;
    color: var(--brand-green);
  }

  .wave { position: absolute; left: 0; top: 0; width: 637px; height: 363px; }

  .contact-phone {
    position: absolute;
    left: 0; width: 637px; top: 286px;
    display: flex; justify-content: center; align-items: center; gap: 6px;
    color: var(--card-white);
    font-size: 20px;
    letter-spacing: 0.5px;
  }
  .contact-line {
    position: absolute;
    left: 0; width: 637px; top: 323px;
    display: flex; justify-content: center; align-items: center; gap: 10px;
    color: var(--card-white);
    font-size: 14px;
    letter-spacing: -0.5px;
  }
  .contact-item { display: flex; align-items: center; gap: 6px; }
  .icon { flex: none; }

  .card--back .wordmark { left: 364px; width: 250px; top: 246px; }
  .card--back .wordmark__top { font-size: 26px; }
  .card--back .wordmark__bottom { font-size: 35px; }
  .card--back .rule { left: 428px; width: 102px; top: 318px; }
  .web-address {
    position: absolute;
    left: 340px; width: 290px; top: 330px;
    text-align: center;
    font-size: 17px;
    letter-spacing: -0.4px;
    color: var(--ink);
  }
  .web-address__domain { color: var(--brand-green); }
</style>
</head>
<body>

  <section class="card card--front" aria-label="Business card front">
    <svg class="wave" viewBox="0 0 637 363" aria-hidden="true">
      <path d="M0,170 C40,250 140,270 260,262 C380,250 480,210 637,203 L637,363 L0,363 Z" fill="var(--brand-green)"/>
      <path d="M0,186 C45,252 150,282 290,273 C420,262 520,220 637,226" fill="none" stroke="var(--card-white)" stroke-width="11"/>
      <path d="M0,188 C45,254 150,284 290,275 C420,264 520,222 637,227" fill="none" stroke="var(--swoosh-grey)" stroke-width="4"/>
    </svg>

    <div class="brand-square" role="img" aria-label="Company logo symbol area"></div>
    <div class="wordmark">
      <span class="wordmark__top">quillmark</span>
      <span class="wordmark__bottom">homesteads.</span>
    </div>
    <div class="rule"></div>
    <div class="holder-name">Derek Tolvane</div>

    <div class="contact-phone">
      <svg class="icon" width="18" height="18" viewBox="0 0 18 18" aria-hidden="true">
        <circle cx="9" cy="9" r="8" fill="none" stroke="#fff" stroke-width="1.3"/>
        <path d="M7,4.5 L8.5,7 L7.5,8 C8,9.5 8.5,10 10,10.5 L11,9.5 L13.5,11 L12.5,13 C8,12.5 5.5,10 5,5.5 Z" fill="#fff"/>
      </svg>
      <span>0217394062</span>
    </div>

    <div class="contact-line">
      <span class="contact-item">
        <svg class="icon" width="15" height="12" viewBox="0 0 15 12" aria-hidden="true">
          <path d="M1,5 L7.5,1 L14,5 L14,11 L1,11 Z" fill="#fff"/>
          <path d="M1,5 L7.5,9 L14,5" fill="none" stroke="var(--brand-green)" stroke-width="1"/>
        </svg>
        dtolvane@quillmarkhomesteads.co.nz
      </span>
      <span class="contact-item">
        <svg class="icon" width="14" height="14" viewBox="0 0 14 14" aria-hidden="true">
          <g fill="none" stroke="#fff" stroke-width="1">
            <circle cx="7" cy="7" r="6"/>
            <ellipse cx="7" cy="7" rx="2.6" ry="6"/>
            <path d="M1,7 H13 M2,4 H12 M2,10 H12"/>
          </g>
        </svg>
        www.quillmarkhomesteads.co.nz
      </span>
    </div>
  </section>

  <section class="card card--back" aria-label="Business card back">
    <div class="brand-square" role="img" aria-label="Large company logo symbol area"></div>
    <div class="wordmark">
      <span class="wordmark__top">quillmark</span>
      <span class="wordmark__bottom">homesteads.</span>
    </div>
    <div class="rule"></div>
    <div class="web-address">www.<span class="web-address__domain">quillmarkhomesteads</span>.co.nz</div>
  </section>

</body>
</html>
```